bamboo kettle vietnamese restaurant in need of a new menu

a family owned vietnamese restaurant in need of a new menu design that is fun, classy, and yet simple. menu that will catch the customers eyes. easy to read yet flows nicely. like to use the color green (basil green color) creme yellow and maroon. open to other colors as long as it looks nice together. our restaurant is family oriented, casual yet has a nice ambiance atmosphere.
prefer 11x17 portrait double sided. attached is our menu with the current price updated so use the info on this to start creating! looking for something unique, professional and one of a kind menu!
Updates
please use your own creative layout and design. we are open to ideas. the files uploaded are the updated prices and the logo is to use whichever one you feel goes with the menu.
Reason: don't see anything we like so far...please be creative!
Target Market(s)
restaurant consumers
Industry/Entity Type
Restaurant
Look and feel

```html
<!DOCTYPE html>
<html lang="en">
<head>
<meta charset="UTF-8">
<title>Bamboo Kettle — Menu</title>
<link href="https://fonts.googleapis.com/css2?family=Oswald:wght@300;400;500&family=Caveat+Brush&family=Montserrat:wght@400;500&display=swap" rel="stylesheet">
<style>
  :root{
    --basil:#78bd45;
    --basil-deep:#5c9f31;
    --basil-soft:#8dc95e;
    --ink:#2a2a2a;
    --ink-soft:#555;
    --paper:#ffffff;
    --paper-grey:#e8e8e8;
    --backdrop:#a4a7ae;
  }
  *{box-sizing:border-box;margin:0;padding:0}
  html,body{width:1200px;height:800px;overflow:hidden}
  body{background:var(--backdrop);font-family:'Oswald',sans-serif;color:var(--ink)}
  .spread{display:flex;gap:14px;padding:20px;height:800px;justify-content:center}
  .panel{width:378px;height:760px;position:relative;overflow:hidden;background:var(--paper)}
  .script-title{font-family:'Caveat Brush',cursive;color:var(--basil);font-weight:400;text-align:center;line-height:1}
  .intro{font-size:8px;text-transform:uppercase;line-height:1.25;font-weight:300;letter-spacing:.1px}
  .menu-list{list-style:none;display:grid;gap:7px 12px}
  .cols-2{grid-template-columns:1fr 1fr}
  .item{display:flex;gap:5px;font-size:8px;line-height:1.22}
  .num{font-weight:400;min-width:14px;font-size:9px}
  .item-name{font-size:9px;font-weight:500;text-transform:uppercase}
  .price{color:var(--basil);font-weight:400;margin-left:3px}
  .item-desc{font-weight:300;text-transform:uppercase}

  /* Appetizers panel */
  .panel--appetizers{background:var(--paper-grey)}
  .appetizers{padding:22px 18px 0}
  .appetizers .script-title{font-size:40px;margin-bottom:10px}
  .appetizers .intro{margin-bottom:10px}
  .salad-intro{margin:14px 0 10px}
  .noodle-soup{position:absolute;left:0;right:0;bottom:0;height:330px;background:var(--basil);padding:0 18px 12px;color:#f4f9ef}
  .noodle-soup .script-title{color:var(--ink);text-align:left;font-size:38px;margin-top:-24px}
  .section-label{font-size:10px;letter-spacing:2px;margin-top:-2px}
  .section-sub{font-size:7px;text-transform:uppercase;opacity:.85;margin-bottom:10px}
  .noodle-soup .price{color:#fffbe0}
  .noodle-soup .menu-list{gap:6px}
  .noodle-soup .split{display:grid;grid-template-columns:1fr 1fr;gap:6px 12px;margin-top:6px}

  /* Pho & Bun panel */
  .pho{padding:20px 18px 0}
  .pho .script-title{font-size:52px}
  .pho-sub{text-align:center;font-family:'Montserrat',sans-serif;font-size:8px;letter-spacing:.5px;margin-bottom:12px}
  .pho .menu-list{gap:6px 12px}
  .extras-band{position:relative;margin:14px 0 16px;height:96px}
  .extras-bg{position:absolute;left:0;top:6px;width:220px;height:84px;background:var(--basil)}
  .extras-list{position:absolute;left:12px;top:14px;list-style:none;color:#fff;font-size:6.5px;line-height:1.35;text-transform:uppercase;font-weight:300}
  .bowl{position:absolute;left:170px;top:0;width:96px;height:96px;border-radius:50%;border:4px solid #fff;background:radial-gradient(circle at 45% 45%,#c9b07a 0%,#a88c54 45%,#e7e0cf 75%);box-shadow:0 2px 6px rgba(0,0,0,.25)}
  .stripe{position:absolute;height:8px;background:var(--basil);border-radius:0 4px 4px 0}
  .bun-head{display:flex;gap:6px;align-items:flex-start;padding:0 18px;margin-bottom:14px}
  .bun-word{font-size:34px;color:var(--basil);font-weight:500;line-height:.9;letter-spacing:-1px}
  .bun-title{font-size:11px;text-transform:uppercase}
  .bun-head .intro{font-size:7.5px}
  .bun{padding:0 18px}

  /* Cover panel */
  .cover-art{position:absolute;inset:0}
  .brand{position:absolute;left:0;right:0;top:505px;display:flex;justify-content:center;align-items:center;gap:10px}
  .brand-mark{width:12px;height:12px;background:var(--basil)}
  .brand-name{font-family:'Montserrat',sans-serif;font-weight:500;font-size:30px;color:var(--ink)}
  .contact{position:absolute;left:22px;bottom:40px;font-size:10px;line-height:1.5;list-style:none}
  .contact li{display:flex;align-items:center;gap:6px}
  .contact svg{width:9px;height:9px;fill:var(--basil)}
</style>
</head>
<body>
<main class="spread">

  <!-- Appetizers & Hu Tieu -->
  <section class="panel panel--appetizers">
    <div class="appetizers">
      <h2 class="script-title">Appetizers</h2>
      <p class="intro">Spring rolls (2) comes with lettuce, vermicelli noodles rolled in rice paper served with peanut sauce with choice of: (cannot be mixed)</p>
      <ol class="menu-list cols-2">
        <li class="item"><span class="num">1.</span><div><h4 class="item-name">Goi Cuon Tom &amp; Thit Heo<span class="price">4.50</span></h4><p class="item-desc">Shrimp &amp; pork spring rolls</p></div></li>
        <li class="item"><span class="num">6.</span><div><h4 class="item-name">Gio Tom (4)<span class="price">5.95</span></h4><p class="item-desc">Fried shrimp rolls</p></div></li>
        <li class="item"><span class="num">2.</span><div><h4 class="item-name">Goi Cuon Thit Heo / Ga / or Bo Nuong<span class="price">5.50</span></h4><p class="item-desc">Choice of: grilled pork / grilled chicken or grilled beef spring rolls</p></div></li>
        <li class="item"><span class="num">7.</span><div><h4 class="item-name">Ca Vien Chien (8)<span class="price">4.95</span></h4><p class="item-desc">Fried fish balls</p></div></li>
        <li class="item"><span class="num">3.</span><div><h4 class="item-name">Bi Cuon<span class="price">4.50</span></h4><p class="item-desc">Pork skin roasted with rice powder spring rolls</p></div></li>
        <li class="item"><span class="num">8.</span><div><h4 class="item-name">Chao Tom (2)<span class="price">7.95</span></h4><p class="item-desc">Grilled shrimp paste wrapped around sugar cane stick</p></div></li>
        <li class="item"><span class="num">4.</span><div><h4 class="item-name">Cha Gio (2)<span class="price">4.50</span></h4><p class="item-desc">Fried eggrolls with shrimp, pork &amp; vegetables rolled in egg wrap</p></div></li>
        <li class="item"><span class="num">9.</span><div><h4 class="item-name">Wonton Soup<span class="price">(S) 4.95 (L) 7.50</span></h4><p class="item-desc">Wonton shrimp &amp; pork soup</p></div></li>
        <li class="item"><span class="num">5.</span><div><h4 class="item-name">Canh Ga Nuoc Mam (6)<span class="price">7.95</span></h4><p class="item-desc">Fried chicken wings</p></div></li>
        <li class="item"><span class="num">10.</span><div><h4 class="item-name">Tom Cua Soup<span class="price">(S) 4.95 (L) 7.50</span></h4><p class="item-desc">Crab meat, shrimp &amp; egg soup</p></div></li>
      </ol>
      <p class="intro salad-intro">Vietnamese salad comes with thin cabbage, carrots, onions, mints, crushed peanuts tossed in lime juice &amp; vinegar with the following choices of:</p>
      <ol class="menu-list cols-2">
        <li class="item"><span class="num">11.</span><div><h4 class="item-name">Goi Ga<span class="price">8.95</span></h4><p class="item-desc">Chicken salad</p></div></li>
        <li class="item"><span class="num">13.</span><div><h4 class="item-name">Bo Tai Chanh<span class="price">11.95</span></h4><p class="item-desc">Rare thin sliced beef with onions, mints, basils, crushed peanuts in lime juice &amp; vinegar</p></div></li>
        <li class="item"><span class="num">12.</span><div><h4 class="item-name">Goi Tom<span class="price">9.95</span></h4><p class="item-desc">Shrimp salad</p></div></li>
        <li class="item"><span class="num">14.</span><div><h4 class="item-name">Chim Cut Roti<span class="price">11.95</span></h4><p class="item-desc">Roasted quails served with salt &amp; pepper</p></div></li>
      </ol>
    </div>

    <div class="noodle-soup">
      <h2 class="script-title">Hu Tieu (mi)</h2>
      <p class="section-label">NOODLE SOUP</p>
      <p class="section-sub">Pork broth with rice or egg noodle</p>
      <ol class="menu-list">
        <li class="item"><span class="num">15.</span><div><h4 class="item-name">Hu Tieu / Mi Dac Biet<span class="price">10.50</span></h4><p class="item-desc">Choice of: rice or egg noodle with shrimp, roast pork, chicken, imitation crab, quail eggs, ground pork &amp; fried shrimp cracker combination noodle soup</p></div></li>
        <li class="item"><span class="num">16.</span><div><h4 class="item-name">Hu Tieu / Mi Hai San<span class="price">11.50</span></h4><p class="item-desc">Choice of: rice or egg noodle with shrimp, scallop, squid, fish balls &amp; imitation crab noodle soup</p></div></li>
        <li class="item"><span class="num">17.</span><div><h4 class="item-name">Hu Tieu My Tho<span class="price">9.95</span></h4><p class="item-desc">Shrimp, roast pork, chicken, fish ball, imitation crab &amp; ground pork with clear noodle soup</p></div></li>
        <li class="item"><span class="num">18.</span><div><h4 class="item-name">Hu Tieu Sate<span class="price">9.50</span></h4><p class="item-desc">Choice of: rice or egg noodle with shrimp, roast pork, chicken, imitation crab, ground pork and fried shrimp cracker with soup on the side</p></div></li>
      </ol>
      <div class="split">
        <ol class="menu-list">
          <li class="item"><span class="num">19.</span><div><h4 class="item-name">Hu Tieu / Mi Kho Dac Biet<span class="price">10.95</span></h4><p class="item-desc">Fried chicken wings</p></div></li>
          <li class="item"><span class="num">20.</span><div><h4 class="item-name">Mi Hoanh Thanh<span class="price">8.95</span></h4><p class="item-desc">Wonton with egg noodle soup</p></div></li>
          <li class="item"><span class="num">21.</span><div><h4 class="item-name">+ Xa Xiu (Roast Pork)<span class="price">10.95</span></h4></div></li>
        </ol>
        <ol class="menu-list">
          <li class="item"><span class="num">22.</span><div><h4 class="item-name">Banh Canh Tom Thit Gio Heo<span class="price">9.50</span></h4><p class="item-desc">Shrimp, pork knuckle &amp; vietnamese big noodle soup</p></div></li>
          <li class="item"><span class="num">23.</span><div><h4 class="item-name">Banh Canh Ga<span class="price">8.95</span></h4><p class="item-desc">Chicken with vietnamese big noodle soup</p></div></li>
        </ol>
      </div>
    </div>
  </section>

  <!-- Pho & Bun -->
  <section class="panel panel--pho">
    <div class="pho">
      <h2 class="script-title">Pho</h2>
      <p class="pho-sub">RICE NOODLES SOUP</p>
      <ol class="menu-list cols-2">
        <li class="item"><span class="num">24.</span><div><h4 class="item-name">Pho Dac Biet<span class="price">9.50</span></h4><p class="item-desc">Steak, brisket, flank, tendon, tripe &amp; meatballs combination noodle soup</p></div></li>
        <li class="item"><span class="num">29.</span><div><h4 class="item-name">Pho Do Bien<span class="price">11.50</span></h4><p class="item-desc">Shrimp, scallop, squid, fish balls, imitation crab &amp; vegetables seafood noodle soup</p></div></li>
        <li class="item"><span class="num">25.</span><div><h4 class="item-name">Pho<span class="price">8.50</span></h4><p class="item-desc">Noodle soup with choices up to 3 items: steak, brisket, flank, tendon, tripe, meatball or vegetables</p></div></li>
        <li class="item"><span class="num">30.</span><div><h4 class="item-name">Pho Tom<span class="price">9.75</span></h4><p class="item-desc">Shrimp with mixed vegetables noodle soup</p></div></li>
        <li class="item"><span class="num">26.</span><div><h4 class="item-name">Pho Ga Vietnam (Ga Di Bo)<span class="price">10.50</span></h4><p class="item-desc">Free range chicken noodle soup</p></div></li>
        <li class="item"><span class="num">31.</span><div><h4 class="item-name">Pho Do Bien Chua Cay<span class="price">11.50</span></h4><p class="item-desc">Shrimp, scallop, squid, fish balls &amp; imitation crab in hot &amp; sour noodle soup</p></div></li>
        <li class="item"><span class="num">27.</span><div><h4 class="item-name">Pho Ga My<span class="price">9.50</span></h4><p class="item-desc">White chicken &amp; mixed vegetables noodle soup</p></div></li>
        <li class="item"><span class="num">32.</span><div><h4 class="item-name">Pho Tre Em<span class="price">7.25</span></h4><p class="item-desc">Kid's steak &amp; meatball noodle soup</p></div></li>
        <li class="item"><span class="num">28.</span><div><h4 class="item-name">Pho Thit Heo / Bo / or Ga Nuong<span class="price">10.50</span></h4><p class="item-desc">Choice of: grilled pork, grilled beef or grilled chicken with mixed vegetables noodle soup</p></div></li>
      </ol>
    </div>

    <div class="extras-band">
      <div class="extras-bg"></div>
      <ul class="extras-list">
        <li>+ Large bowl add 2.00</li>
        <li>+ Extra meat add 3.00</li>
        <li>+ Extra shrimp add 3.00</li>
        <li>+ Extra vegetables add 1.50</li>
        <li>+ Extra rice noodles add 1.50</li>
        <li>+ Add fried egg 1.50</li>
        <li>+ Add egg roll 1.25</li>
      </ul>
      <div class="stripe" style="left:250px;top:22px;width:128px"></div>
      <div class="stripe" style="left:258px;top:40px;width:100px"></div>
      <div class="stripe" style="left:258px;top:58px;width:80px"></div>
      <div class="stripe" style="left:250px;top:76px;width:60px"></div>
      <div class="bowl" role="img" aria-label="Photo of a bowl of pho with beef and rice noodles"></div>
    </div>

    <div class="bun-head">
      <span class="bun-word">BUN</span>
      <div>
        <h3 class="bun-title">Vermicelli Noodle Bowl</h3>
        <p class="intro">All vermicelli bowl comes with fresh lettuce, bean sprouts, sliced cucumbers, shredded carrots &amp; crushed peanuts</p>
      </div>
    </div>
    <div class="bun">
      <ol class="menu-list cols-2">
        <li class="item"><span class="num">33.</span><div><h4 class="item-name">Bun Dac Biet<span class="price">12.95</span></h4><p class="item-desc">Choice of: grilled pork, grilled chicken or grilled beef with grilled shrimp &amp; fried eggroll special combination vermicelli bowl</p></div></li>
        <li class="item"><span class="num">38.</span><div><h4 class="item-name">Bun Cha Gio (3)<span class="price">9.50</span></h4><p class="item-desc">Fried eggroll vermicelli bowl</p></div></li>
        <li class="item"><span class="num">34.</span><div><h4 class="item-name">Bun - Vermicelli Bowl<span class="price">9.50</span></h4><p class="item-desc">Choice of: grilled pork, grilled chicken or grilled beef</p></div></li>
        <li class="item"><span class="num">39.</span><div><h4 class="item-name">Bun Chao Tom (2)<span class="price">9.50</span></h4><p class="item-desc">Grilled shrimp paste vermicelli bowl</p></div></li>
        <li class="item"><span class="num">35.</span><div><h4 class="item-name">+ Eggroll<span class="price">9.50</span></h4></div></li>
        <li class="item"><span class="num">40.</span><div><h4 class="item-name">Bun Bo Hue<span class="price">9.50</span></h4><p class="item-desc">Spicy beef noodle soup with beef shank, pork knuckle, pork blood with large vermicelli noodles</p></div></li>
        <li class="item"><span class="num">36.</span><div><h4 class="item-name">+ Shrimp<span class="price">10.50</span></h4></div></li>
        <li class="item"><span class="num">41.</span><div><h4 class="item-name">Bun Rieu<span class="price">9.50</span></h4><p class="item-desc">Mixed ground pork &amp; crab, pork blood, dried tofu with vermicelli rice noodle in tomato broth soup</p></div></li>
        <li class="item"><span class="num">37.</span><div><h4 class="item-name">Bun Tom Nuong (8)<span class="price">10.50</span></h4><p class="item-desc">Grilled shrimp with vermicelli noodle bowl</p></div></li>
        <li class="item"><span class="num">42.</span><div><h4 class="item-name">Bun Mang Vit<span class="price">9.50</span></h4><p class="item-desc">Duck &amp; bamboo vermicelli noodle soup</p></div></li>
      </ol>
    </div>
  </section>

  <!-- Cover -->
  <section class="panel panel--cover">
    <svg class="cover-art" viewBox="0 0 378 760" aria-hidden="false">
      <defs>
        <linearGradient id="coverPhotoTone" x1="0" y1="0" x2="1" y2="1">
          <stop offset="0" stop-color="#b98f6a"/>
          <stop offset=".35" stop-color="#c9372b"/>
          <stop offset=".6" stop-color="#6fa84a"/>
          <stop offset="1" stop-color="#d9d3bd"/>
        </linearGradient>
      </defs>
      <path role="img" aria-label="Photo of a red bowl of noodle soup topped with fresh herbs, bean sprouts, chilies and lime" d="M0 0 H378 V360 C300 392 130 362 0 262 Z" fill="url(#coverPhotoTone)"/>
      <path d="M0 274 C130 374 300 404 378 372" fill="none" stroke="var(--basil)" stroke-width="5"/>
    </svg>
    <div class="brand">
      <span class="brand-mark"></span>
      <span class="brand-name">Bamboo Kettle</span>
    </div>
    <ul class="contact">
      <li><svg viewBox="0 0 24 24"><path d="M6.6 10.8a15.1 15.1 0 0 0 6.6 6.6l2.2-2.2a1 1 0 0 1 1-.25 11.4 11.4 0 0 0 3.6.57 1 1 0 0 1 1 1V20a1 1 0 0 1-1 1A17 17 0 0 1 3 4a1 1 0 0 1 1-1h3.5a1 1 0 0 1 1 1c0 1.25.2 2.45.57 3.57a1 1 0 0 1-.25 1z"/></svg>(555) 210-4418</li>
      <li><svg viewBox="0 0 24 24"><path d="M12 2a7 7 0 0 0-7 7c0 5.25 7 13 7 13s7-7.75 7-13a7 7 0 0 0-7-7zm0 9.5A2.5 2.5 0 1 1 12 6.5a2.5 2.5 0 0 1 0 5z"/></svg>1280 Willow Park Ave, Palm Grove, FL 33000</li>
    </ul>
  </section>

</main>
</body>
</html>
```